Website for vegan focused blog

A website is needed so that I can launch my new blog in Dubai. It will be mainly vegan focused but also lifestyle based. Wordpress based- i started to build a site on Wordpress but design is not my forte ;)
Main content on the site will be; my recipes, reviews of products/restaurants, lifestyle posts and travel.
For this I ask for a homepage design, a recipe design page that includes a recipe card and a generic page for posts that can show pictures and videos. Also a contact me page.
Main headers should be: Home, Recipes and happy for suggestions.
Must look clean and neat but appealing, happy for minimalist look. I like pink and grey colours. Must be Wordpress compatible.
Have attached a couple of example posts for reference
Must have social links etc.
name of blog is: Maren by the dunes
Other blogs I like are: https://quietladleoven.com/ https://wellfernkitchen.com/ https://wellfernkitchen.com/ https://www.ohladycakes.com/https://beetsatsupper.com/ https://dorintalve.com/

Target Market(s)

Residents in the UAE. General individuals interested in vegan meals, plant based nutrition, travel and reviews.

Number of Pages Required

4 page

Colors
eea4c8
eda3c7
f9d9e8
dbdbdb
aaaaaa
d5d5d5

Requirements
Must have
• Recipe page- must include recipe card plug in option
• Social media integration
• Email sign ups

```html
<!DOCTYPE html>
<html lang="en">
<head>
<meta charset="utf-8">
<title>Maren by the dunes</title>
<link rel="stylesheet" href="https://fonts.googleapis.com/css2?family=Playfair+Display:ital,wght@0,400;1,400;1,700&family=Lato:wght@400;700&display=swap">
<style>
:root{
  --pink:#eea4c8;
  --pink-strong:#eda3c7;
  --pink-soft:#f9d9e8;
  --line:#dbdbdb;
  --line-soft:#e8e8e8;
  --grey:#aaaaaa;
  --grey-mid:#d5d5d5;
  --ink:#3c3c3c;
  --ink-soft:#5a5a5a;
  --footer-bg:#f7f7f7;
  --photo:linear-gradient(120deg,#1f3a22 0%,#2f4a2a 22%,#5a3a30 45%,#6e4337 60%,#c2442f 78%,#e9e3dc 100%);
}
*{box-sizing:border-box;margin:0;padding:0}
html,body{width:1200px;height:2812px;overflow:hidden;background:#fff}
body{position:relative;font-family:'Lato',sans-serif;color:var(--ink);font-size:11.5px;line-height:1.6}
.abs{position:absolute}
.photo{background:var(--photo);display:block}

/* header */
.site-title{top:34px;left:0;width:1200px;text-align:center;font-family:'Playfair Display',serif;font-style:italic;font-size:34px;color:var(--pink);line-height:1}
.main-nav{top:114px;left:0;width:1200px;height:38px;border-top:1px solid var(--line-soft);border-bottom:1px solid var(--line-soft);display:flex;justify-content:center;align-items:center;gap:44px;font-family:'Playfair Display',serif;font-style:italic;font-weight:700;font-size:12px;color:var(--ink)}
.search-icon{position:absolute;right:234px;top:12px}

/* main post */
.post-title{font-family:'Playfair Display',serif;color:var(--pink);font-size:19px;text-align:center;line-height:1.2}
.rule{width:22px;height:1px;background:var(--grey);margin:0 auto}
.date{font-size:7.5px;letter-spacing:1px;text-transform:uppercase;color:var(--grey);text-align:center}
.featured-post{top:198px;left:234px;width:506px}
.featured-post .rule{margin:12px auto 10px}
.featured-post .photo{height:352px;margin-top:18px}
.post-body p{margin-top:15px;font-size:9.8px;line-height:1.75;color:var(--ink-soft)}
.post-meta{display:flex;align-items:center;border-top:1px solid var(--line-soft);border-bottom:1px solid var(--line-soft);height:34px;font-size:7.5px;color:var(--ink);letter-spacing:.5px}
.post-meta .tags{margin-left:40px;color:var(--grey)}
.post-meta .tags b{color:var(--ink);font-weight:400}
.share{display:flex;gap:9px;margin-left:auto}
.share i{width:7px;height:7px;border-radius:50%;background:var(--ink);display:block}

/* two column cards */
.card{width:240px}
.card .photo{height:178px}
.card-title{font-family:'Playfair Display',serif;color:var(--pink);font-size:14px;line-height:1.35;text-align:center;margin-top:28px}
.card .rule{margin:10px auto 8px}
.excerpt{font-size:9.6px;line-height:1.65;color:var(--ink-soft);margin-top:10px}
.card-foot{display:flex;align-items:center;font-size:7px;letter-spacing:.5px;margin-top:12px;padding:0 6px}

/* wide feature */
.wide-feature{top:1365px;left:234px;width:506px;height:360px}
.wide-feature .photo{height:317px}
.wide-caption{position:absolute;left:62px;top:268px;width:380px;height:92px;background:#fff;border:1px solid var(--pink);display:flex;align-items:center;justify-content:center;text-align:center;padding:0 30px;font-family:'Playfair Display',serif;font-weight:400;color:var(--pink);font-size:16px;line-height:1.45}

/* list posts */
.list-post{left:234px;width:506px;height:146px;display:flex;gap:19px}
.list-post .photo{width:203px;height:146px;flex:none}
.list-post .body{flex:1}
.list-post .card-title{text-align:left;margin-top:-2px;font-size:13.5px}
.list-post .rule{margin:12px 0 8px}
.list-post .date{text-align:left;font-size:6.5px}
.list-post .excerpt{margin-top:12px}
.list-post .card-foot{padding:0;margin-top:14px}

.pager{top:2522px;left:0;width:1200px;display:flex;justify-content:center;gap:24px;font-size:7.5px;letter-spacing:.8px}
.pager span{display:flex;align-items:center;gap:8px}
.pager .newer{color:var(--grey)}

/* sidebar */
.widget{left:778px;width:188px;border:1px solid var(--line-soft);padding:18px 12px 12px;overflow:hidden}
.widget-title{font-family:'Playfair Display',serif;font-style:italic;font-weight:400;color:var(--pink);font-size:11px;line-height:1.5;margin-bottom:10px}
.about .photo{height:90px;background:linear-gradient(180deg,#c9b7a6 0%,#8a7a6c 45%,#2e2b2a 100%)}
.about p{font-size:8.3px;text-align:center;line-height:1.5;margin-top:9px;color:var(--ink-soft)}
.socials{display:flex;gap:10px;padding-left:10px;margin-top:14px}
.socials i{width:20px;height:20px;border-radius:50%;background:var(--pink);display:block}
.email-field{height:30px;border:1px solid var(--line);font-size:7.5px;color:var(--grey);display:flex;align-items:center;padding-left:10px;margin-top:14px}
.pink-btn{height:28px;background:var(--pink-soft);color:#fff;font-size:7.5px;letter-spacing:.8px;display:flex;align-items:center;justify-content:center;margin-top:10px;text-transform:uppercase}
.feed-grid{display:grid;grid-template-columns:1fr 1fr;gap:4px}
.feed-grid .photo{height:80px}
.feed .pink-btn{text-transform:none;letter-spacing:0;font-size:9px;margin-top:12px;background:var(--pink);height:26px}
.latest-item{display:flex;gap:8px;margin-bottom:16px}
.latest-item .photo{width:56px;height:44px;flex:none}
.latest-item h4{font-family:'Playfair Display',serif;font-style:italic;font-weight:400;font-size:8.5px;line-height:1.35;color:var(--ink)}
.latest-item small{display:block;font-size:6px;letter-spacing:1px;color:var(--grey);margin-top:7px}

/* footer */
.site-footer{top:2612px;left:0;width:1200px;height:200px;background:var(--footer-bg)}
.footer-title{position:absolute;top:36px;width:100%;text-align:center;font-family:'Playfair Display',serif;font-style:italic;font-size:30px;color:var(--pink)}
.footer-socials{position:absolute;top:110px;width:100%;display:flex;justify-content:center;gap:10px}
.footer-socials i{width:24px;height:24px;border-radius:50%;background:var(--pink);display:block}
.copyright{position:absolute;top:160px;left:0;width:100%;border-top:1px solid var(--line-soft);padding-top:12px;text-align:center;font-size:7.5px;color:var(--grey)}
</style>
</head>
<body>

<header>
  <div class="abs site-title">Maren by the dunes</div>
  <nav class="abs main-nav">
    <span>Home</span><span>About</span><span>Recipes</span><span>Reviews of products</span><span>Lifestyle</span><span>Travel</span><span>Contact</span>
    <svg class="search-icon" width="12" height="12" viewBox="0 0 12 12"><circle cx="5" cy="5" r="3.8" fill="none" stroke="#3c3c3c" stroke-width="1.4"/><line x1="7.8" y1="7.8" x2="11" y2="11" stroke="#3c3c3c" stroke-width="1.6"/></svg>
  </nav>
</header>

<main>
  <article class="abs featured-post">
    <h1 class="post-title">Mushroom Steak</h1>
    <div class="rule"></div>
    <div class="date">Saturday, September 8, 2018</div>
    <div class="photo" role="img" aria-label="Grilled portobello mushroom steak with roasted tomato, steamed spinach and a creamy dip"></div>
    <div class="post-body">
      <p>Steak and vegan don't go in the same sentence BUT trust me on this... a decent sized Portobello shroom cooked just right with a blend of delicious marinade, it has the meatiest texture and its delicious as well oh and did we mention it is completely cruelty free!?</p>
      <p>To get the right texture you need the right tools so I always suggest cooking this on a griddle pan or even on the BBQ to give it that additional boost of flavours.</p>
      <p>When my non vegan friends are looking for something to cook when they have the plant powered team over for dinner, I always use this as a suggestion. The sides can be mixed and matched so in this instance I have used a grilled tomato and a pile of steamed spinach but you can add fries or salad or anything else that would be served alongside a steak. So all in all, it is a very versatile dish.</p>
    </div>
    <div class="post-meta" style="margin-top:28px">
      <span>12 COMMENTS</span>
      <span class="tags"><b>TAGGED:</b> &nbsp;Food, mushroom, balsamic vinegar, olive oil, cumin, paprika, spinach</span>
      <span class="share"><i></i><i></i><i></i><i></i><i></i></span>
    </div>
  </article>

  <article class="abs card" style="top:932px;left:234px">
    <div class="photo" role="img" aria-label="Mushroom steak plate with tomato and spinach"></div>
    <h2 class="card-title">Lorem ipsum dolor sit amet consectetur elit</h2>
    <div class="rule"></div>
    <div class="date">Saturday, September 8, 2018</div>
    <p class="excerpt">Aliquam vestibulum, magna at interdum iaculis, orci nulla liquam est, ac feugiat ligula diam vitae nisl. In dictum, odio at dictumina, dolor diam maximus lacus, in auctor dui risus. Morbi tinci unted mauris, ac imperdiet nibh malesuada utorbi cursus massa ...</p>
    <div class="card-foot"><span>12 COMMENTS</span><span class="share"><i></i><i></i><i></i><i></i><i></i></span></div>
  </article>

  <article class="abs card" style="top:932px;left:499px">
    <div class="photo" role="img" aria-label="Mushroom steak plate with tomato and spinach"></div>
    <h2 class="card-title">Lorem ipsum dolor sit amet consectetur elit</h2>
    <div class="rule"></div>
    <div class="date">Saturday, September 8, 2018</div>
    <p class="excerpt">Aliquam vestibulum, magna at interdum iaculis, orci nulla liquam est, ac feugiat ligula diam vitae nisl. In dictum, odio at dictumina, dolor diam maximus lacus, in auctor dui risus. Morbi tinci unted mauris, ac imperdiet nibh malesuada utorbi cursus massa ...</p>
    <div class="card-foot"><span>12 COMMENTS</span><span class="share"><i></i><i></i><i></i><i></i><i></i></span></div>
  </article>

  <article class="abs wide-feature">
    <div class="photo" role="img" aria-label="Close view of a grilled mushroom steak with spinach and tomato"></div>
    <h2 class="wide-caption">Sed sit amet justo mauris, arcumattis rutrum eleifend vulputate dolor</h2>
  </article>

  <article class="abs list-post" style="top:1772px">
    <div class="photo" role="img" aria-label="Mushroom steak with roasted tomato"></div>
    <div class="body">
      <h2 class="card-title">Lorem ipsum dolor sit amet consectetur elit</h2>
      <div class="rule"></div>
      <div class="date">Saturday, September 8, 2018</div>
      <p class="excerpt">Aliquam vestibulum, magna at interdum iaculis, orci nulla liquam est, ac feugiat ligula diam vitae nisl. In dictum, odio at dictumina, dolor diam maximus lacus, in auctor dui risus. Morbi tinci unted mauris, ac imperdiet nibh malesuada utorbi cursus massa ...</p>
      <div class="card-foot"><span>12 COMMENTS</span><span class="share"><i></i><i></i><i></i><i></i><i></i></span></div>
    </div>
  </article>

  <article class="abs list-post" style="top:1950px">
    <div class="photo" role="img" aria-label="Mushroom steak with roasted tomato"></div>
    <div class="body">
      <h2 class="card-title">Lorem ipsum dolor sit amet consectetur elit</h2>
      <div class="rule"></div>
      <div class="date">Saturday, September 8, 2018</div>
      <p class="excerpt">Aliquam vestibulum, magna at interdum iaculis, orci nulla liquam est, ac feugiat ligula diam vitae nisl. In dictum, odio at dictumina, dolor diam maximus lacus, in auctor dui risus. Morbi tinci unted mauris, ac imperdiet nibh malesuada utorbi cursus massa ...</p>
      <div class="card-foot"><span>12 COMMENTS</span><span class="share"><i></i><i></i><i></i><i></i><i></i></span></div>
    </div>
  </article>

  <article class="abs list-post" style="top:2128px">
    <div class="photo" role="img" aria-label="Mushroom steak with roasted tomato"></div>
    <div class="body">
      <h2 class="card-title">Lorem ipsum dolor sit amet consectetur elit</h2>
      <div class="rule"></div>
      <div class="date">Saturday, September 8, 2018</div>
      <p class="excerpt">Aliquam vestibulum, magna at interdum iaculis, orci nulla liquam est, ac feugiat ligula diam vitae nisl. In dictum, odio at dictumina, dolor diam maximus lacus, in auctor dui risus. Morbi tinci unted mauris, ac imperdiet nibh malesuada utorbi cursus massa ...</p>
      <div class="card-foot"><span>12 COMMENTS</span><span class="share"><i></i><i></i><i></i><i></i><i></i></span></div>
    </div>
  </article>

  <article class="abs list-post" style="top:2306px">
    <div class="photo" role="img" aria-label="Mushroom steak with roasted tomato"></div>
    <div class="body">
      <h2 class="card-title">Lorem ipsum dolor sit amet consectetur elit</h2>
      <div class="rule"></div>
      <div class="date">Saturday, September 8, 2018</div>
      <p class="excerpt">Aliquam vestibulum, magna at interdum iaculis, orci nulla liquam est, ac feugiat ligula diam vitae nisl. In dictum, odio at dictumina, dolor diam maximus lacus, in auctor dui risus. Morbi tinci unted mauris, ac imperdiet nibh malesuada utorbi cursus massa ...</p>
      <div class="card-foot"><span>12 COMMENTS</span><span class="share"><i></i><i></i><i></i><i></i><i></i></span></div>
    </div>
  </article>

  <nav class="abs pager">
    <span><svg width="14" height="6" viewBox="0 0 14 6"><path d="M14 3H1M3.5 .5L1 3l2.5 2.5" fill="none" stroke="#3c3c3c" stroke-width="1"/></svg>OLDER POSTS</span>
    <span class="newer">NEWER POSTS<svg width="14" height="6" viewBox="0 0 14 6"><path d="M0 3h13M10.5 .5L13 3l-2.5 2.5" fill="none" stroke="#aaaaaa" stroke-width="1"/></svg></span>
  </nav>
</main>

<aside>
  <section class="abs widget about" style="top:182px;height:240px">
    <h3 class="widget-title">About Maren by the dunes</h3>
    <div class="photo" role="img" aria-label="Figure standing on a beach at sunset"></div>
    <p>On Maren by the dunes, I share some delicious recipes either my own or from other fabulous sites that I have come across, my meal plans, reviews of products and restaurants that I visit and more.<br>More &rarr;</p>
  </section>

  <section class="abs widget" style="top:450px;height:94px">
    <h3 class="widget-title">Subscribe &amp; Follow</h3>
    <div class="socials"><i></i><i></i><i></i><i></i><i></i></div>
  </section>

  <section class="abs widget" style="top:568px;height:144px">
    <h3 class="widget-title">Newsletter</h3>
    <div class="email-field">Your Email Address</div>
    <div class="pink-btn">Subscribe</div>
  </section>

  <section class="abs widget feed" style="top:738px;height:354px">
    <h3 class="widget-title">Snapfolio</h3>
    <div class="feed-grid">
      <div class="photo" role="img" aria-label="Feed photo of a mushroom dish"></div>
      <div class="photo" role="img" aria-label="Feed photo of a mushroom dish"></div>
      <div class="photo" role="img" aria-label="Feed photo of a mushroom dish"></div>
      <div class="photo" role="img" aria-label="Feed photo of a mushroom dish"></div>
      <div class="photo" role="img" aria-label="Feed photo of a mushroom dish"></div>
      <div class="photo" role="img" aria-label="Feed photo of a mushroom dish"></div>
    </div>
    <div class="pink-btn">Follow on Snapfolio &nbsp;&rarr;</div>
  </section>

  <section class="abs widget" style="top:1114px;height:294px">
    <h3 class="widget-title">Latest posts</h3>
    <div class="latest-item"><div class="photo" role="img" aria-label="Mushroom steak thumbnail"></div><div><h4>Maecenas sodales dignissim liberoid sodales</h4><small>LIFESTYLE</small></div></div>
    <div class="latest-item"><div class="photo" role="img" aria-label="Mushroom steak thumbnail"></div><div><h4>Maecenas sodales dignissim liberoid sodales</h4><small>TRAVEL</small></div></div>
    <div class="latest-item"><div class="photo" role="img" aria-label="Mushroom steak thumbnail"></div><div><h4>Maecenas sodales dignissim liberoid sodales</h4><small>LIFESTYLE</small></div></div>
    <div class="latest-item"><div class="photo" role="img" aria-label="Mushroom steak thumbnail"></div><div><h4>Maecenas sodales dignissim liberoid sodales</h4><small>TRAVEL</small></div></div>
  </section>
</aside>

<footer class="abs site-footer">
  <div class="footer-title">Maren by the dunes</div>
  <div class="footer-socials"><i></i><i></i><i></i><i></i><i></i></div>
  <div class="copyright">Copyright © 2018 Maren by the dunes. All Right Reserved. Privacy Policy | Terms of Service</div>
</footer>

</body>
</html>
```